Financial Advisor Resource Firm needs business card design

Need business card design for company in Omaha NE called Meridale Circle. We provide resources to financial advisors....workshop programs, retirement analysis, and insurance planning. I would like to see designs that use grays, greens, black, and white colors. The final design should communicate 'collaboration' and be simple yet attractive to financial planning clients. I will attached our logo and another picture of a puzzle piece coming together. I would like the incorporate the puzzle picture somehow, maybe on the back somehow, with color or just the gray scale....OR, the picture be the front of the card with 'Meridale' definition on it (see upload) and then company logo, employee name, title, address on the back (see ppt uploaded). The following disclosure needs to be included somewhere- Advisory services offered through Stonebrook Assets, LLC.
Updates

I uploaded a svg and ai file of the logo

Target Market(s)

Financial planning clients and financial advisors....so pretty diverse age range of about 40-70.

Industry/Entity Type

Financial Planning

Contact Information for Business Card

Tobias L. Fenwright, MBA
Founder/President
5287 E. Larkin Road
Suite 230
Omaha, NE 68190
Phone- (402) 555-0147
Cell- (402) 555-0183
Fax- (402) 555-0129
email- tobias@meridaleplan.example
web address- www.meridaleplan.example

Colors
1b1b1b
474747
d3d3d3
ffffff
9bcb3c
abd036

Requirements
Must have
• Must include logo provided, must be 2 sided, and must have disclosure...all of these items listed in project description

```html
<!DOCTYPE html>
<html lang="en">
<head>
<meta charset="utf-8">
<title>Meridale Circle — Business Card</title>
<link rel="stylesheet" href="https://fonts.googleapis.com/css2?family=Lato:wght@400;700&display=swap">
<style>
  :root {
    --green: #86c23a;
    --green-soft: #94c94a;
    --ink: #1b1b1b;
    --white: #ffffff;
    --backdrop: #5a5a5a;
  }
  * { margin: 0; padding: 0; box-sizing: border-box; }
  html, body { width: 1200px; height: 802px; overflow: hidden; }
  body {
    background: var(--backdrop);
    font-family: "Lato", Arial, sans-serif;
    position: relative;
  }
  .card {
    position: absolute;
    top: 274px;
    width: 443px;
    height: 265px;
    box-shadow: 2px 3px 6px rgba(0,0,0,0.45);
    overflow: hidden;
  }
  /* Front */
  .card--front { left: 136px; background: var(--white); }
  .front__band {
    position: absolute; left: 0; top: 0; bottom: 0; width: 55px;
    background: var(--green);
    border-right: 2px solid var(--ink);
  }
  .brand {
    position: absolute; right: 26px; top: 40px;
    display: flex; align-items: center; gap: 8px;
  }
  .brand__dot { width: 14px; height: 14px; border-radius: 50%; background: var(--green); }
  .brand__name {
    font-size: 21px; font-weight: 400; color: var(--ink);
    letter-spacing: 1px; text-transform: uppercase;
  }
  .contact {
    position: absolute; left: 79px; top: 101px;
    color: var(--ink); font-size: 12.5px; line-height: 15px;
  }
  .contact__name {
    color: var(--green); font-size: 14.5px; font-weight: 700;
    text-transform: uppercase; line-height: 17px;
  }
  .contact__name small { font-size: 12px; font-weight: 400; }
  .contact__title { margin-bottom: 5px; }
  .contact__list { list-style: none; }
  .contact__list li { display: flex; align-items: center; gap: 5px; }
  .contact__list svg { width: 10px; height: 10px; fill: var(--green); flex: none; }
  .contact__address { margin-top: 5px; padding-left: 3px; }
  /* Back */
  .card--back { left: 624px; background: var(--green); }
  .back__pattern {
    position: absolute; inset: 0;
    background: linear-gradient(180deg, var(--green-soft), var(--green));
  }
  .back__mark {
    position: absolute; left: 256px; top: 117px;
    width: 46px; height: 46px; border-radius: 50%;
    border: 5px solid var(--white);
  }
  .back__disclosure {
    position: absolute; left: 0; right: 0; top: 226px;
    text-align: center; color: var(--white);
    font-size: 11px; font-weight: 700; text-transform: uppercase;
  }
</style>
</head>
<body>
  <section class="card card--front">
    <div class="front__band"></div>
    <div class="brand">
      <span class="brand__dot"></span>
      <span class="brand__name">Meridale Circle</span>
    </div>
    <div class="contact">
      <div class="contact__name">Tobias L. Fenwright, <small>MBA</small></div>
      <div class="contact__title">Founder/President</div>
      <ul class="contact__list">
        <li><svg viewBox="0 0 10 10"><path d="M1 3c0-1 2-2 4-2s4 1 4 2v1H7V3H3v1H1zM2 5h6l1 4H1z"/></svg>(402) 555-0147</li>
        <li><svg viewBox="0 0 10 10"><path d="M3 0h4a1 1 0 0 1 1 1v8a1 1 0 0 1-1 1H3a1 1 0 0 1-1-1V1a1 1 0 0 1 1-1zm0 1.5v6h4v-6z"/></svg>(402) 555-0183</li>
        <li><svg viewBox="0 0 10 10"><path d="M3 0h4v3H3zM1 3.5h8v4H7V6H3v1.5H1zM3 7h4v3H3z"/></svg>(402) 555-0129</li>
        <li><svg viewBox="0 0 10 10"><path d="M0 2h10v6H0zM1 3l4 3 4-3v-.3L5 5 1 2.7z" fill-rule="evenodd"/></svg>tobias@meridaleplan.example</li>
        <li><svg viewBox="0 0 10 10"><circle cx="5" cy="5" r="4.5"/></svg>www.meridaleplan.example</li>
      </ul>
      <div class="contact__address">5287 E. Larkin Road<br>Suite 230 Omaha, NE 68190</div>
    </div>
  </section>

  <section class="card card--back">
    <div class="back__pattern" role="img" aria-label="Repeating faint pattern of the brand symbol across the green back"></div>
    <div class="back__mark"></div>
    <p class="back__disclosure">Advisory services offered through Stonebrook Assets, LLC.</p>
  </section>
</body>
</html>
```